Moxy Fen needs some awesome stationary

Do you have what it takes to get my brand? You either do or you don't, have a crack at a design and you my just win my business.

I don't want to waste your or my time, so put your creative genius on either a business card or envelope.

I however need a package of stationary that follows the same brand. I will message you to complete the remaining should I like your first submission.

Here is what I need, have a go!

Basically I need the following for my small business based in melbourne.
- Letterhead (printer ready and MS Word)
- Business Card
- Compliments Slip
- Envelope
- Proposal Cover Page (MS Word only)
- Presentation Folder
- Marbled Fox Cards
- Student Name Tent
- Index Cards
- Vell-Ka

I am establishing the brand and it must be modern, professional but also relaxed; that is not formal and not corporate. It represents a company are leaders, but small enough to care and operate like a bunch of friends. We are bringing people and conversations back to business, and turfing out all the bureaucracy and crazy and wasteful procedures. Its about "lets talk and figure it out together and find even better ways".

Target Market(s)

Mainly companies that build software products, but Agile practices are used in many other industries (even graphic design projects)

Industry/Entity Type

Information Technology

Font styles to use
Sans Serif

Colors
3176b5
aaaaaa

Requirements
Must have
• I like curves and circles and not boxes or rectangles.
• I want a colour rich design with my brand colours, but it must be balanced.
• I want more modern than traditional, but simple modern
Should not have
• Not corporate
• Please don't waste my time if your not going to think about it.
• Don't mess with my primary logo
• Don't change my colours
• Don't overlay logo on image

```html
<!DOCTYPE html>
<html lang="en">
<head>
<meta charset="utf-8">
<title>Moxy Fen — Business Card</title>
<link href="https://fonts.googleapis.com/css2?family=Open+Sans:wght@400;600;700&display=swap" rel="stylesheet">
<style>
  :root {
    --brand-blue: #2d5ca6;
    --brand-grey: #9aa1ad;
    --card-white: #ffffff;
    --backdrop: #dcd7d1;
    --text-light: #ffffff;
  }
  * { box-sizing: border-box; margin: 0; padding: 0; }
  html, body {
    width: 1200px;
    height: 987px;
    overflow: hidden;
    background: var(--backdrop);
    font-family: "Open Sans", sans-serif;
  }
  .canvas { position: relative; width: 1200px; height: 987px; }

  .card {
    position: absolute;
    left: 292px;
    width: 616px;
    height: 352px;
    overflow: hidden;
    box-shadow: 0 3px 10px rgba(0,0,0,0.25);
  }
  .card--front { top: 130px; }
  .card--back  { top: 505px; }
  .card-shapes { position: absolute; inset: 0; }

  /* Front */
  .contact-block {
    position: absolute;
    left: 37px;
    top: 43px;
    color: var(--text-light);
  }
  .person-name { font-size: 19px; font-weight: 700; letter-spacing: 0.3px; line-height: 24px; }
  .person-role { font-size: 15px; line-height: 21px; }
  .postal { margin-top: 16px; font-size: 15px; line-height: 21px; }
  .channels { list-style: none; margin-top: 14px; }
  .channels li {
    display: flex; align-items: center; gap: 9px;
    font-size: 15px; line-height: 23px;
  }
  .channels li.hotline { font-size: 19px; line-height: 26px; }
  .channels svg { width: 14px; height: 14px; flex: none; fill: var(--text-light); }

  .brand-name {
    position: absolute;
    left: 340px;
    width: 262px;
    top: 120px;
    text-align: center;
    color: var(--brand-blue);
    font-size: 40px;
    font-weight: 700;
    letter-spacing: 0.5px;
  }

  /* Back */
  .back-wordmark,
  .back-web {
    position: absolute;
    top: 176px;
    transform: translate(-50%, -50%) rotate(-90deg);
    white-space: nowrap;
    color: var(--text-light);
  }
  .back-wordmark {
    left: 518px;
    font-size: 50px;
    line-height: 50px;
    font-weight: 700;
  }
  .back-web {
    left: 580px;
    font-size: 14px;
    line-height: 14px;
    letter-spacing: 3.6px;
  }
</style>
</head>
<body>
<main class="canvas">

  <section class="card card--front" aria-label="Business card front">
    <svg class="card-shapes" viewBox="0 0 616 352" width="616" height="352" aria-hidden="true">
      <rect width="616" height="352" fill="var(--brand-blue)"/>
      <path d="M358,0 C290,40 268,150 288,222 C304,290 338,328 362,352 L616,352 L616,0 Z" fill="var(--card-white)"/>
      <path d="M296,140 C302,250 350,322 376,352 L528,352 C420,338 320,280 296,140 Z" fill="var(--brand-grey)"/>
    </svg>

    <div class="contact-block">
      <p class="person-name">DANA KESTREL</p>
      <p class="person-role">CEO</p>
      <p class="person-role">Professional Scrum Trainer</p>
      <p class="postal">PO Box 4127<br>Elmswood Vale<br>VIC 3999, Australia</p>
      <ul class="channels">
        <li class="hotline">
          <svg viewBox="0 0 16 16"><path d="M3.5 1l2.6 3-1.5 1.8c.8 1.9 2.3 3.5 4.3 4.5l1.7-1.5 3 2.6-1.6 2.4C6.8 13.4 2.4 8.8 1 3z"/></svg>
          13000MOXYF
        </li>
        <li>
          <svg viewBox="0 0 16 16"><path d="M4 0h8v16H4zM5.5 2v10h5V2zM7 13.2h2v1.4H7z" fill-rule="evenodd"/></svg>
          +61 412 555 018
        </li>
        <li>
          <svg viewBox="0 0 16 16"><path d="M1 3h14v10H1zM1.5 3.5L8 9l6.5-5.5" /><path d="M1 3l7 5.5L15 3z" fill="var(--brand-blue)"/></svg>
          dana@moxy-fen.com.au
        </li>
        <li>
          <svg viewBox="0 0 16 16"><circle cx="8" cy="8" r="7"/><path d="M4 5c2 0 2 2 4 2s1 3-1 4c-1 1-1 3-2 3M10 2c0 2 3 2 3 4" stroke="var(--brand-blue)" stroke-width="1.4" fill="none"/></svg>
          www.moxy-fen.com.au
        </li>
      </ul>
    </div>

    <p class="brand-name">Moxy Fen</p>
  </section>

  <section class="card card--back" aria-label="Business card back">
    <svg class="card-shapes" viewBox="0 0 616 352" width="616" height="352" aria-hidden="true">
      <rect width="616" height="352" fill="var(--brand-blue)"/>
      <rect width="284" height="352" fill="var(--card-white)"/>
      <circle cx="284" cy="176" r="185" fill="var(--card-white)"/>
    </svg>
    <p class="back-wordmark">Moxy Fen</p>
    <p class="back-web">www.moxy-fen.com.au</p>
  </section>

</main>
</body>
</html>
```